Mobile Fitness snd Therapy Business Card Design

I need a business card designed for my mobile fitness and therapy business.

Please view the images that I have uploaded. I like the simplicity of the design that I have attached. I adapted it with my information

Target Market(s)

Those seeking personal training, injury rehabilitation or massage therapy.

Industry/Entity Type

Business

Contact Information for Business Card

Derek Fulham - MSc, CAT(C), RMT, CSCS, Pn2
e-mail: derek@vantrelo.com
website: www.vantrelo.com
instagram: @derek_fulham

Font styles to use
Sans Serif

Colors
3176b5
0355a3

Requirements
Must have
• "Contact us to receive a FREE assessment"
• Services offered:
• Personal Training
• Golf Fitness
• Injury Rehab
• Massage Therapy
• Yoga
Nice to have
• Consistent colours with brand
• - Dark Blue: #232837
• - Blue: #5096f0
• Consistent look/feel with the website: www.vantrelo.com

```html
<!DOCTYPE html>
<html lang="en">
<head>
<meta charset="utf-8">
<title>Vantrelo Business Card</title>
<link href="https://fonts.googleapis.com/css2?family=Roboto:wght@400;500;700&display=swap" rel="stylesheet">
<style>
  :root {
    --navy: #232837;
    --blue: #5096f0;
    --blue-deep: #2a5fd4;
    --blue-light: #8fc0f8;
    --brand-blue: #3176b5;
    --name-blue: #1f5fd0;
    --ink: #2b2f3a;
    --white: #ffffff;
    --backdrop: #e9ebef;
  }
  * { box-sizing: border-box; margin: 0; padding: 0; }
  html, body { width: 1200px; height: 900px; overflow: hidden; }
  body {
    background: var(--backdrop);
    font-family: "Roboto", Arial, sans-serif;
    display: flex;
    flex-direction: column;
    align-items: center;
    justify-content: center;
    gap: 40px;
  }
  .card {
    position: relative;
    width: 700px;
    height: 400px;
    overflow: hidden;
    box-shadow: 0 6px 18px rgba(0,0,0,0.18);
  }

  /* Back of card */
  .card-back { background: var(--navy); color: var(--white); text-align: center; }
  .card-back .brand { position: absolute; top: 70px; left: 0; right: 0; }
  .wordmark {
    font-weight: 700;
    letter-spacing: 6px;
    line-height: 1;
  }
  .card-back .wordmark { font-size: 62px; color: var(--white); }
  .tagline {
    font-weight: 700;
    letter-spacing: 3px;
    margin-top: 8px;
  }
  .card-back .tagline { font-size: 17px; color: var(--white); }
  .offer-band {
    position: absolute;
    top: 205px; left: 0; right: 0;
    height: 44px;
    background: var(--blue);
    display: flex; align-items: center; justify-content: center;
    font-size: 16px; font-weight: 700; letter-spacing: 0.5px;
  }
  .services { position: absolute; top: 268px; left: 0; right: 0; }
  .services-title {
    font-size: 18px; font-weight: 700; color: var(--blue);
    letter-spacing: 0.5px; margin-bottom: 10px;
  }
  .services-list { font-size: 16px; line-height: 1.45; letter-spacing: 0.5px; }

  /* Front of card */
  .card-front { background: var(--white); color: var(--ink); }
  .waves { position: absolute; inset: 0; }
  .holder { position: absolute; top: 48px; left: 58px; }
  .holder-name { font-size: 29px; font-weight: 700; color: var(--name-blue); }
  .holder-creds { font-size: 19px; margin-top: 4px; }
  .card-front .brand { position: absolute; top: 96px; right: 46px; text-align: left; }
  .card-front .wordmark { font-size: 52px; color: var(--navy); letter-spacing: 5px; }
  .card-front .tagline { font-size: 14px; color: var(--navy); letter-spacing: 2.6px; }
  .contact-list {
    position: absolute; top: 218px; left: 66px;
    list-style: none; font-size: 19px; line-height: 31px;
  }
  .contact-list li { display: flex; align-items: center; gap: 9px; }
  .contact-icon { width: 18px; height: 18px; flex: none; }
</style>
</head>
<body>

<section class="card card-back">
  <div class="brand">
    <div class="wordmark">VANTRELO</div>
    <div class="tagline">NUTRITION - FITNESS - HEALTH</div>
  </div>
  <div class="offer-band">CONTACT US TO RECEIVE A FREE ASSESSMENT</div>
  <div class="services">
    <div class="services-title">SERVICES OFFERED:</div>
    <div class="services-list">
      PERSONAL TRAINING &nbsp;| GOLF FITNESS | INJURY REHAB<br>
      MASSAGE THERAPY &nbsp;| YOGA
    </div>
  </div>
</section>

<section class="card card-front">
  <svg class="waves" viewBox="0 0 700 400" preserveAspectRatio="none" aria-hidden="true">
    <path class="wave-mid" d="M0 352 C 240 362, 420 310, 520 236 C 590 186, 640 160, 700 138 L700 400 L0 400 Z" fill="var(--blue)"/>
    <path class="wave-gap" d="M0 374 C 250 380, 430 325, 530 252 C 600 203, 650 182, 700 166 L700 400 L0 400 Z" fill="var(--white)"/>
    <path class="wave-deep" d="M0 386 C 260 392, 445 336, 542 262 C 612 212, 656 193, 700 180 L700 400 L0 400 Z" fill="var(--blue-deep)"/>
    <path class="wave-light" d="M0 336 C 200 346, 350 306, 480 236 C 370 318, 210 356, 0 350 Z" fill="var(--blue-light)"/>
  </svg>

  <div class="holder">
    <div class="holder-name">DEREK FULHAM</div>
    <div class="holder-creds">MSc, CAT(C), RMT, CSCS, Pn2</div>
  </div>

  <div class="brand">
    <div class="wordmark">VANTRELO</div>
    <div class="tagline">NUTRITION - FITNESS - HEALTH</div>
  </div>

  <ul class="contact-list">
    <li>
      <svg class="contact-icon" viewBox="0 0 18 18" aria-hidden="true">
        <rect x="1" y="3" width="16" height="12" rx="1.5" fill="var(--name-blue)"/>
        <path d="M2 4.5 L9 10 L16 4.5" fill="none" stroke="var(--white)" stroke-width="1.4"/>
      </svg>
      derek@vantrelo.com
    </li>
    <li>
      <svg class="contact-icon" viewBox="0 0 18 18" aria-hidden="true">
        <circle cx="9" cy="9" r="8" fill="var(--name-blue)"/>
        <ellipse cx="9" cy="9" rx="3.5" ry="7.5" fill="none" stroke="var(--white)" stroke-width="1.2"/>
        <line x1="1.5" y1="9" x2="16.5" y2="9" stroke="var(--white)" stroke-width="1.2"/>
      </svg>
      www.vantrelo.com
    </li>
    <li>
      <svg class="contact-icon" viewBox="0 0 18 18" aria-hidden="true">
        <rect x="1" y="1" width="16" height="16" rx="3" fill="var(--name-blue)"/>
      </svg>
      @derek_fulham
    </li>
  </ul>
</section>

</body>
</html>
```